Shopify ecommerce Custom Web page

We are using Shopify for our ecommerce system for some our products lines and we need the pages to be designed to match a new website that we are building. These pages will need to effective promote our e-learning products.

The designer will need to incorporate the design into Shopify along with the coding required to ensure the site is functional.

Reason: It was not completed by the previous bidder.

The project has been reopened and we have added an additional $200. Please response interest for those who have already bid and additionally those who have not.

Requirements
Must have
• The shopify site needs to be functional as the deliverable for this project

```html
<!DOCTYPE html>
<html lang="en">
<head>
<meta charset="utf-8">
<title>LEARNVAULT – E-learning Assets</title>
<link rel="stylesheet" href="https://fonts.googleapis.com/css2?family=Figtree:wght@400;500&family=Open+Sans:wght@400;600;700&family=Source+Sans+3:wght@400;600;700&display=swap">
<style>
:root{
  --ink:#1f1f1f;
  --topbar:#1d1f21;
  --header:#979797;
  --hero-dark:#2a2a2a;
  --hero-mid:#6d6d6d;
  --blue:#1a9bd7;
  --blue-dark:#0f7bb0;
  --white:#ffffff;
  --card-line:#e2e2e2;
  --text:#2b2b2b;
  --footer:#2b2b2b;
  --footer-base:#1f1f1f;
  --footer-text:#a9a9a9;
  --footer-rule:#4a4a4a;
  --page-red:#d4262b;
}
*{margin:0;padding:0;box-sizing:border-box}
html,body{width:1147px;height:1200px;overflow:hidden;background:var(--white)}
body{position:relative;font-family:"Figtree",sans-serif;color:var(--text)}
.abs{position:absolute}

/* top bar */
.topbar{left:0;top:0;width:1147px;height:34px;background:var(--topbar)}
.search{left:713px;top:7px;width:149px;height:21px;background:var(--white);font-size:10px;color:#777;padding:4px 7px}
.search-btn{left:862px;top:7px;width:25px;height:21px;background:var(--blue)}
.search-btn svg{display:block;margin:3px auto}
.cart-icon{left:898px;top:10px}
.cart-text{left:926px;top:11px;font-size:10px;color:#cfcfcf}

/* header */
.header{left:0;top:34px;width:1147px;height:72px;background:var(--header)}
.logo{left:156px;top:48px;font-family:"Source Sans 3",sans-serif;font-weight:700;font-size:33px;letter-spacing:.3px;color:var(--white);line-height:1}
.nav{left:488px;top:62px;display:flex;gap:19.5px;font-family:"Source Sans 3",sans-serif;font-weight:700;font-size:13px;color:var(--white)}

/* hero */
.hero{left:0;top:106px;width:1147px;height:296px;background:radial-gradient(ellipse at 60% 40%,var(--hero-mid),var(--hero-dark) 75%)}
.hero-figure{left:159px;top:130px;width:282px;height:272px;background:linear-gradient(160deg,#f4f4f4,#d9d9d9);border-radius:40px 40px 0 0;opacity:.92}
.hero-title{left:520px;top:143px;font-family:"Open Sans",sans-serif;font-weight:700;font-size:26px;color:var(--white);white-space:nowrap}
.hero-text{left:521px;top:183px;width:560px;font-family:"Open Sans",sans-serif;font-size:19.5px;line-height:27px;color:var(--white)}
.hero-btn{left:523px;top:285px;width:179px;height:48px;background:var(--blue);border-bottom:4px solid var(--blue-dark);font-family:"Open Sans",sans-serif;font-size:23px;color:var(--white);text-align:center;line-height:46px}
.tab{top:368px;height:34px;background:var(--white);font-family:"Source Sans 3",sans-serif;font-weight:700;font-size:14px;color:var(--ink);text-align:center;line-height:36px;white-space:nowrap}
.tab.active{background:var(--blue);color:var(--white)}
.tab-pointer{left:224px;top:402px;width:0;height:0;border-left:6px solid transparent;border-right:6px solid transparent;border-top:7px solid var(--blue)}
.dot{top:380px;width:11px;height:11px;border-radius:50%;background:var(--white)}
.dot.current{background:var(--ink);border:1px solid var(--ink)}

/* intro */
.intro-title{left:156px;top:419px;font-size:15.5px;font-weight:500;color:var(--ink)}
.intro-text{left:157px;top:441px;width:850px;font-size:12.2px;line-height:20px;color:var(--text)}

/* products */
.card{width:192px;height:154px;border:1px solid var(--card-line);border-radius:3px;background:linear-gradient(#fff 80%,#eeeeee);box-shadow:0 1px 2px rgba(0,0,0,.06)}
.card-art{position:absolute;left:26px;top:16px;width:140px;height:112px;border-radius:6px}
.art-tablet{background:linear-gradient(135deg,#5a5a5a,#bdbdbd)}
.art-book{background:linear-gradient(135deg,#9ac45a,#3a3a3a)}
.art-headset{background:linear-gradient(135deg,#1f1f1f,#6a6a6a)}
.art-box{background:linear-gradient(135deg,#f2cc2a,#2a4d9c)}
.card-title{width:192px;text-align:center;font-size:15.5px;color:var(--blue)}
.card-text{width:192px;text-align:center;font-size:12.4px;line-height:17px;color:var(--text)}

/* pagination */
.pager{left:476px;top:959px;height:30px;display:flex;border:1px solid #d6d6d6;border-radius:15px;overflow:hidden;background:#fafafa}
.pager span{width:28px;height:28px;line-height:28px;text-align:center;font-size:12.5px;color:#555;border-left:1px solid #dedede}
.pager span:first-child{border-left:none}
.pager .current{color:var(--page-red);font-weight:500}

/* footer */
.footer{left:0;top:1006px;width:1147px;height:163px;background:var(--footer)}
.footer-base{left:0;top:1169px;width:1147px;height:31px;background:var(--footer-base);text-align:center;line-height:31px;font-size:10px;color:#9a9a9a}
.footer-base a{color:#9a9a9a;text-decoration:none;margin-left:8px}
.f-head{font-family:"Source Sans 3",sans-serif;font-weight:600;font-size:13px;color:var(--blue);padding-bottom:5px;border-bottom:1px solid var(--footer-rule);width:118px;white-space:nowrap}
.f-head.plain{border-bottom:none;width:auto}
.f-links{list-style:none;font-size:11.5px;color:var(--footer-text)}
.f-links li{height:23px}
.news-text{left:575px;top:1043px;width:210px;font-size:11.5px;line-height:16.5px;color:var(--footer-text)}
.field{top:1083px;width:109px;height:25px;background:var(--white);font-size:9.5px;color:#888;padding:7px 9px}
.subscribe{left:693px;top:1115px;width:108px;height:28px;background:var(--blue);border-bottom:3px solid var(--blue-dark);color:var(--white);font-size:12.5px;text-align:center;line-height:27px}
.social{left:860px;display:flex;align-items:center;gap:10px;font-size:11.5px;color:var(--footer-text)}
.social i{display:block;width:31px;height:31px;border-radius:50%;background:#5a5a5a}
</style>
</head>
<body>

<div class="abs topbar"></div>
<div class="abs search">Search</div>
<div class="abs search-btn"><svg width="14" height="14" viewBox="0 0 14 14"><circle cx="6" cy="6" r="4.3" fill="none" stroke="#fff" stroke-width="1.8"/><line x1="9.2" y1="9.2" x2="13" y2="13" stroke="#fff" stroke-width="2"/></svg></div>
<svg class="abs cart-icon" width="22" height="15" viewBox="0 0 22 15"><path d="M1 4h20l-2 10H3z" fill="#e8b93a"/><path d="M4 4l4-3M18 4l-4-3" stroke="#e8b93a" stroke-width="1.5"/></svg>
<div class="abs cart-text">0 Cart Items</div>

<div class="abs header"></div>
<div class="abs logo">LEARNVAULT</div>
<nav class="abs nav"><span>Home</span><span>Connecting</span><span>E-learning Assets</span><span>Content in Motion</span><span>About Us</span><span>Contact Us</span></nav>

<section class="abs hero"></section>
<div class="abs hero-figure" role="img" aria-label="White pictogram of a presenter raising one arm"></div>
<h1 class="abs hero-title">Lorem Ipsum is simply dummy text</h1>
<p class="abs hero-text">Lorem Ipsum is simply dummy text of the printing and typesetting industry. Lorem Ipsum has been the industry's standard dummy text ever since the 1500s.</p>
<div class="abs hero-btn">LEARN MORE</div>

<div class="abs tab active" style="left:157px;width:146px">STORYBOARD ASSETS</div>
<div class="abs tab" style="left:309px;width:90px">PACKAGES</div>
<div class="abs tab" style="left:405px;width:88px">BENEFITS</div>
<div class="abs tab" style="left:499px;width:166px">SLIDESHOW LINKAGE</div>
<div class="abs tab" style="left:672px;width:72px">ABOUT</div>
<div class="abs tab-pointer"></div>
<div class="abs dot current" style="left:920px"></div>
<div class="abs dot" style="left:936px"></div>
<div class="abs dot" style="left:952px"></div>
<div class="abs dot" style="left:969px"></div>

<h2 class="abs intro-title">DISCRIPTIVE</h2>
<p class="abs intro-text">Lorem Ipsum is simply dummy text of the printing and typesetting industry. Lorem Ipsum has been the industry's standard dummy text ever since the 1500s, when an unknown printer took a galley of type and scrambled it to make a type specimen book. It has survived not only five centuries</p>

<!-- row 1 -->
<div class="abs card" style="left:158px;top:494px"><div class="card-art art-tablet" role="img" aria-label="Tablet showing an e-learning screen with a coming soon badge"></div></div>
<div class="abs card" style="left:368px;top:494px"><div class="card-art art-book" role="img" aria-label="Science textbook next to a tablet edition"></div></div>
<div class="abs card" style="left:578px;top:494px"><div class="card-art art-headset" role="img" aria-label="Black virtual reality headset"></div></div>
<div class="abs card" style="left:788px;top:494px"><div class="card-art art-box" role="img" aria-label="Maths and science software box with disc"></div></div>

<div class="abs card-title" style="left:158px;top:657px">DISCRIPTIVE</div>
<div class="abs card-title" style="left:368px;top:657px">DISCRIPTIVE</div>
<div class="abs card-title" style="left:578px;top:657px">DISCRIPTIVE</div>
<div class="abs card-title" style="left:788px;top:657px">DISCRIPTIVE</div>
<p class="abs card-text" style="left:160px;top:677px">Lorem Ipsum is simply dummy<br>text of the printing</p>
<p class="abs card-text" style="left:370px;top:677px">Lorem Ipsum is simply dummy<br>text of the printing</p>
<p class="abs card-text" style="left:580px;top:677px">Lorem Ipsum is simply dummy<br>text of the printing</p>
<p class="abs card-text" style="left:790px;top:677px">Lorem Ipsum is simply dummy<br>text of the printing</p>

<!-- row 2 -->
<div class="abs card" style="left:159px;top:722px"><div class="card-art art-tablet" role="img" aria-label="Tablet showing an e-learning screen with a coming soon badge"></div></div>
<div class="abs card" style="left:369px;top:722px"><div class="card-art art-book" role="img" aria-label="Science textbook next to a tablet edition"></div></div>
<div class="abs card" style="left:578px;top:722px"><div class="card-art art-headset" role="img" aria-label="Black virtual reality headset"></div></div>
<div class="abs card" style="left:789px;top:722px"><div class="card-art art-box" role="img" aria-label="Maths and science software box with disc"></div></div>

<div class="abs card-title" style="left:158px;top:887px">DISCRIPTIVE</div>
<div class="abs card-title" style="left:368px;top:887px">DISCRIPTIVE</div>
<div class="abs card-title" style="left:578px;top:887px">DISCRIPTIVE</div>
<div class="abs card-title" style="left:788px;top:887px">DISCRIPTIVE</div>
<p class="abs card-text" style="left:160px;top:907px">Lorem Ipsum is simply dummy<br>text of the printing</p>
<p class="abs card-text" style="left:370px;top:907px">Lorem Ipsum is simply dummy<br>text of the printing</p>
<p class="abs card-text" style="left:580px;top:907px">Lorem Ipsum is simply dummy<br>text of the printing</p>
<p class="abs card-text" style="left:790px;top:907px">Lorem Ipsum is simply dummy<br>text of the printing</p>

<div class="abs pager"><span>&#8249;</span><span class="current">1</span><span>2</span><span>3</span><span>4</span><span>5</span><span>&#8250;</span></div>

<footer class="abs footer"></footer>
<div class="abs" style="left:153px;top:1018px">
  <div class="f-head">Quick Links</div>
  <ul class="f-links" style="margin-top:8px"><li>Home</li><li>Connecting learners</li><li>E-learning in Motion</li><li>About Us</li><li>Contact Us</li></ul>
</div>
<div class="abs" style="left:364px;top:1018px">
  <div class="f-head">Support Links</div>
  <ul class="f-links" style="margin-top:8px;padding-left:2px"><li>Legal Notice</li><li>Privacy Policy</li><li>Terms &amp; Conditions</li><li>Help</li></ul>
</div>
<div class="abs" style="left:575px;top:1018px"><div class="f-head plain">Newsletter Subscribe</div></div>
<p class="abs news-text">Sign-up for our daily emails by entering your information below</p>
<div class="abs field" style="left:575px">Name</div>
<div class="abs field" style="left:692px">Email Address</div>
<div class="abs subscribe">Subscribe</div>
<div class="abs" style="left:862px;top:1018px"><div class="f-head">Social</div></div>
<div class="abs social" style="top:1045px"><i></i>Friendwall</div>
<div class="abs social" style="top:1084px"><i></i>Chirpline</div>
<div class="abs social" style="top:1122px"><i></i>Circlenet</div>

<div class="abs footer-base">© 2013 Company Name. <a>Terms of Service</a><a>Privacy</a><a>Sitemap</a></div>

</body>
</html>
```